Business Cards for new orthopaedic surgery practice

My husband and I are starting our own orthopaedic surgery practice. We are looking for a business card that is uniform, but one will have my name/title and the other will have his. You can just create one design with my name on it for now. But when I choose your design as the winning design I will ask that you add another copy with his name/title.

We are looking for classy, simple, elite all in one. We like dark blues/a little gold/yellow. Something that goes with our logo. We want our logo incorporated. Here is all the info you need:
Business name: RV Bone & Vitality Center
Location: 38517 North Willowmere Ave
Maple Harbor, FL 33960
Phone: 954-218-4063
Fax: 954-582-7341
Email: info@myrvbonecare.example

Names: Lydia Vance, M.D.
Board Certified Hand and Upper Extremity Surgeon

Ebo Dansu, M.D.
Board Certified Hip & Knee Replacement/General Orthopaedic Surgeon

Can decide what you want to put on the back. Maybe a slogan:
Grounded in Care. Centered on You

I am just going to upload our logo. The only thing is if we select you as the winning design, the location, and phone numbers may change. We will need your help to update that once fully solidified.

Industry/Entity Type

Medical

Contact Information for Business Card

Colors
0054AA
0677BA
7BADD7
CADEEF
E8F1F8
0094D4
00A9DD
6FCCEA
C7EBF8
E9F6FB

Requirements
Must have
• class, appeal,
Should not have
• We want to air on the side of masculine if we are looking at masculine vs. feminine feel. But we still want it classy, sophisticated, and something we will love

```html
<!DOCTYPE html>
<html lang="en">
<head>
<meta charset="utf-8">
<title>RV Bone &amp; Vitality Center – Business Cards</title>
<link href="https://fonts.googleapis.com/css2?family=Cinzel:wght@500;600&family=Montserrat:wght@400;500;600&display=swap" rel="stylesheet">
<style>
  :root{
    --navy:#1b2a52;
    --gold:#c8a25a;
    --white:#ffffff;
    --ink:#2b3350;
    --bg-top:#d6d6d6;
    --bg-bottom:#a9a9a9;
  }
  *{margin:0;padding:0;box-sizing:border-box}
  html,body{width:1200px;height:802px;overflow:hidden}
  body{background:linear-gradient(180deg,var(--bg-top),var(--bg-bottom));position:relative;font-family:"Montserrat",sans-serif}
  .card{position:absolute;top:246px;width:540px;height:309px;border-radius:22px;overflow:hidden;box-shadow:0 10px 24px rgba(0,0,0,.28)}
  .card--front{left:40px;background:var(--white)}
  .card--back{left:620px;background:var(--navy)}
  .card__shapes{position:absolute;inset:0;width:100%;height:100%}
  .brand{position:absolute;display:flex;align-items:center;justify-content:center;text-align:center;border-radius:50%;font-family:"Cinzel",serif;font-weight:600;letter-spacing:.08em;line-height:1.25}
  .brand--front{left:362px;top:14px;width:116px;height:116px;border:1.5px solid var(--gold);color:var(--navy);font-size:12px}
  .brand--back{left:185px;top:48px;width:170px;height:170px;border:1.5px solid var(--gold);color:var(--white);font-size:17px}
  .holder{position:absolute;left:30px;top:132px}
  .holder__name{font-family:"Cinzel",serif;font-weight:600;font-size:19px;color:var(--gold);letter-spacing:.02em}
  .holder__name .holder__cred{color:var(--navy)}
  .holder__title{margin-top:4px;font-size:11.5px;color:var(--ink);line-height:1.35}
  .contact{position:absolute;left:250px;top:216px;color:var(--white);font-size:11px;line-height:14px}
  .contact__address{margin-bottom:6px}
  .contact__row{display:flex;align-items:center;gap:7px}
  .contact__row svg{width:10px;height:10px;flex:none}
  .tagline{position:absolute;left:0;right:0;top:244px;text-align:center;color:var(--gold);font-weight:600;font-size:17px}
</style>
</head>
<body>
  <section class="card card--front" aria-label="Business card front">
    <svg class="card__shapes" viewBox="0 0 540 309" aria-hidden="true">
      <path d="M110 309 C150 232 250 212 350 187 C450 162 510 142 540 112 L540 309 Z" fill="#1b2a52"/>
      <path d="M100 309 C140 226 245 204 345 179 C445 154 505 132 540 100" fill="none" stroke="#c8a25a" stroke-width="5"/>
    </svg>
    <div class="brand brand--front">RV Bone &amp;<br>Vitality<br>Center</div>
    <div class="holder">
      <p class="holder__name">LYDIA VANCE, <span class="holder__cred">M.D.</span></p>
      <p class="holder__title">Board Certified Hand and Upper<br>Extremity Surgeon</p>
    </div>
    <div class="contact">
      <p class="contact__address">38517 North Willowmere Ave<br>Maple Harbor, FL 33960</p>
      <p class="contact__row"><svg viewBox="0 0 10 10"><path d="M2 1 L4 1 L4.6 3 L3.4 3.8 Q4.4 5.8 6.2 6.6 L7 5.4 L9 6 L9 8 Q5 9 2 6 Q0.5 3.5 2 1Z" fill="#c8a25a"/></svg>954-218-4063</p>
      <p class="contact__row"><svg viewBox="0 0 10 10"><rect x="1" y="3.5" width="8" height="4.5" rx="1" fill="#c8a25a"/><rect x="2.8" y="1" width="4.4" height="3" fill="#c8a25a"/></svg>954-582-7341</p>
      <p class="contact__row"><svg viewBox="0 0 10 10"><rect x="0.8" y="2" width="8.4" height="6" fill="#c8a25a"/><path d="M0.8 2 L5 5.5 L9.2 2" fill="none" stroke="#1b2a52" stroke-width=".8"/></svg>info@myrvbonecare.example</p>
    </div>
  </section>

  <section class="card card--back" aria-label="Business card back">
    <div class="brand brand--back">RV Bone &amp;<br>Vitality<br>Center</div>
    <p class="tagline">Grounded in Care. Centered on You</p>
  </section>
</body>
</html>
```